Tech business card design

We need an amazing business card design for our new business 'Pexla' a marketing tech startup based in Sydney, Australia. We provide an online marketplace for businesses to search and buy advertising media, connect with service providers and learn more about marketing. We wish to communicate 'cool tech', reliability and professionalism and design based around our logo.

Target Market(s)

Business Owners

Contact Information for Business Card

Name
Position
Email Address
Website
Phone Number

Font styles to use
Other font styles liked:
• Avenir & Avenir Next

Colors

Designer to choose colors to be used in the design.

```html
<!DOCTYPE html>
<html lang="en">
<head>
<meta charset="utf-8">
<title>Pexla Business Card</title>
<link rel="stylesheet" href="https://fonts.googleapis.com/css2?family=Nunito+Sans:wght@400;600;800&display=swap">
<style>
  :root {
    --navy: #17174d;
    --navy-deep: #0f0f38;
    --white: #ffffff;
    --ink: #2a2a3a;
    --stage: #1f1f22;
    --edge: #dcdce2;
  }
  * { margin: 0; padding: 0; box-sizing: border-box; }
  html, body {
    width: 1200px; height: 892px; overflow: hidden;
    background: var(--stage);
    font-family: "Nunito Sans", "Avenir Next", Avenir, sans-serif;
  }
  .canvas { position: relative; width: 1200px; height: 892px; }
  .card {
    position: absolute; width: 560px; height: 341px;
    border-radius: 3px; overflow: hidden;
    box-shadow: 0 18px 40px rgba(0,0,0,0.55);
  }
  /* Front */
  .card-front {
    left: 70px; top: 80px;
    background: radial-gradient(ellipse at 50% 35%, #1e1e5c 0%, var(--navy) 55%, var(--navy-deep) 100%);
    color: var(--white);
  }
  .card-front .wordmark {
    position: absolute; left: 0; right: 0; top: 92px;
    text-align: center; font-weight: 800; font-size: 112px;
    letter-spacing: -2px; line-height: 1;
  }
  .card-front .website {
    position: absolute; left: 0; right: 0; top: 262px;
    text-align: center; font-size: 12px; letter-spacing: 7px;
    font-weight: 400;
  }
  /* Back */
  .card-back {
    left: 570px; top: 470px;
    background: var(--white); color: var(--ink);
    box-shadow: 0 18px 40px rgba(0,0,0,0.55), 4px 5px 0 var(--edge);
  }
  .card-back .wordmark {
    position: absolute; right: 70px; top: 22px;
    font-weight: 800; font-size: 84px; letter-spacing: -2px;
    line-height: 1; color: var(--navy);
  }
  .name-band {
    position: absolute; left: 0; top: 104px; width: 268px; height: 54px;
    background: var(--navy); color: var(--white);
    padding: 6px 0 0 26px;
  }
  .band-divider {
    position: absolute; left: 268px; top: 88px; width: 2px; height: 70px;
    background: var(--navy);
  }
  .name-band .person { font-size: 18px; font-weight: 600; line-height: 1.2; }
  .name-band .role { font-size: 14px; font-weight: 400; line-height: 1.2; opacity: .9; }
  .web-tab { position: absolute; right: 0; top: 232px; width: 205px; height: 48px; }
  .web-tab span {
    position: absolute; right: 14px; top: 14px; color: var(--white);
    font-size: 15px; letter-spacing: 0.5px;
  }
  .contact-list {
    position: absolute; left: 26px; top: 272px; list-style: none;
    font-size: 16px; color: var(--ink);
  }
  .contact-list li { display: flex; align-items: center; gap: 10px; height: 24px; }
  .contact-list svg { width: 16px; height: 16px; flex: none; }
</style>
</head>
<body>
<main class="canvas">
  <section class="card card-front" aria-label="Card front">
    <div class="wordmark">pexla</div>
    <div class="website">www.pexlamedia.com.au</div>
  </section>

  <section class="card card-back" aria-label="Card back">
    <div class="wordmark">pexla</div>
    <div class="band-divider"></div>
    <div class="name-band">
      <div class="person">MARCUS REID</div>
      <div class="role">Founder, Director</div>
    </div>
    <div class="web-tab">
      <svg width="205" height="48" viewBox="0 0 205 48" aria-hidden="true">
        <polygon points="10,0 205,0 205,48 0,48 0,14" fill="var(--navy)"/>
      </svg>
      <span>www.pexlamedia.com.au</span>
    </div>
    <ul class="contact-list">
      <li>
        <svg viewBox="0 0 16 16" aria-hidden="true"><rect x="4" y="1" width="8" height="14" rx="1.5" fill="none" stroke="var(--navy)" stroke-width="1.6"/><circle cx="8" cy="12.3" r="0.9" fill="var(--navy)"/></svg>
        +61 (0)412 555 019
      </li>
      <li>
        <svg viewBox="0 0 16 16" aria-hidden="true"><rect x="1" y="4" width="14" height="9" fill="var(--navy)"/><polyline points="1,4 8,9 15,4" fill="none" stroke="var(--white)" stroke-width="1"/></svg>
        marcus@pexlamedia.com.au
      </li>
    </ul>
  </section>
</main>
</body>
</html>
```